Modern Label for cleaning products for the brand Vorlix

We need a label design for our line of cleaning products. The label should feature our logo and an image to identify the product's intended use. I've added our logo and an image for use. This only concerns the design of the label on the front of the bottle.

Label dimensions:
Label 1 (500ml bottle with spray): width 58mm x height 115mm
Label 2: (1L bottle): width 73mm x height 140mm
The design must be consistent for both bottles which you find in the pictures.

The bottles to be labeled are white. See the attachment for a photo of the bottles.

The photo must also appear on the label to identify the product's intended use.

Product information:
Brand: Vorlix
Product: Sanitary Cleaner

This text must be placed on the label:
"Cleans, descales & freshens. followed with this text: "Ideal for quick and powerful cleaning. A ready-to-use product for everyday use."

- Mention the seperate USP's: Sanitary, Bathroom, Toilet, Wet areas

Appearance: This is a consumer product, but it must have a professional appearance. We would like to see a design that use the color blue from our logo.

Target Market(s)

Consumers who take care of their homes and want to maintain it the correct (professional) way

Font styles to use
Sans Serif

Colors
0054AA
0677BA
7BADD7
CADEEF
E8F1F8

Requirements
Must have
• USP's + use of image and logo + blend in 1 design
Nice to have
• Keep the color of the logo in the design
Should not have
• Comic sans

```html
<!DOCTYPE html>
<html lang="en">
<head>
<meta charset="utf-8">
<title>Vorlix Sanitary Cleaner – Labels</title>
<link rel="stylesheet" href="https://fonts.googleapis.com/css2?family=Bebas+Neue&family=Montserrat:ital,wght@0,700;0,900;1,400&display=swap">
<style>
  :root {
    --blue: #1558ac;
    --blue-bright: #0677ba;
    --ink: #1a1a1a;
    --white: #ffffff;
    --sheen: #eef0f3;
    --note-bg: #f0f0f1;
    --stage: #5f5f5f;
  }
  * { margin: 0; padding: 0; box-sizing: border-box; }
  html, body { width: 705px; height: 1200px; overflow: hidden; }
  body {
    background: var(--stage);
    display: flex;
    justify-content: center;
    align-items: center;
    gap: 45px;
  }
  .label {
    width: 300px;
    height: 594px;
    background: var(--white);
    display: flex;
    flex-direction: column;
    overflow: hidden;
  }
  .label-head {
    height: 188px;
    background:
      linear-gradient(125deg, transparent 30%, rgba(255,255,255,.9) 38%, transparent 46%),
      linear-gradient(125deg, #f7f8fa 0%, var(--sheen) 50%, #f9fafb 100%);
    display: flex;
    flex-direction: column;
    align-items: center;
    padding-top: 19px;
  }
  .brand { display: flex; flex-direction: column; align-items: center; }
  .brand-dot {
    width: 50px; height: 50px;
    border-radius: 50%;
    border: 6px solid var(--blue-bright);
  }
  .brand-name {
    font-family: "Montserrat", sans-serif;
    font-weight: 900;
    font-size: 22px;
    color: var(--ink);
    line-height: 1;
    margin-top: 4px;
    letter-spacing: .3px;
  }
  .product-name {
    font-family: "Bebas Neue", sans-serif;
    font-size: 70px;
    line-height: 1;
    color: var(--blue);
    margin-top: 14px;
    letter-spacing: .5px;
  }
  .product-type {
    height: 40px;
    background: var(--blue);
    color: var(--white);
    font-family: "Montserrat", sans-serif;
    font-weight: 900;
    font-size: 31px;
    letter-spacing: 1px;
    text-align: center;
    line-height: 41px;
  }
  .use-photo {
    height: 170px;
    background: linear-gradient(90deg, #8a8c8e 0%, #a9a9a8 28%, #e9eaec 45%, #f4f4f5 70%, #9a9b9d 100%);
  }
  .claim {
    height: 40px;
    background: var(--blue);
    color: var(--white);
    font-family: "Bebas Neue", sans-serif;
    font-size: 27px;
    text-align: center;
    line-height: 43px;
  }
  .label-body {
    flex: 1;
    display: flex;
    flex-direction: column;
    align-items: center;
    padding-top: 21px;
  }
  .note {
    width: 258px;
    background: var(--note-bg);
    border-radius: 6px;
    padding: 9px 0;
    font-family: "Montserrat", sans-serif;
    font-style: italic;
    font-weight: 400;
    font-size: 10.3px;
    line-height: 16px;
    color: var(--ink);
    text-align: center;
  }
  .uses {
    margin-top: 17px;
    font-family: "Bebas Neue", sans-serif;
    font-size: 20px;
    color: var(--ink);
    letter-spacing: -.2px;
    white-space: nowrap;
  }
  .uses .alt { color: var(--blue); }
  .net-weight {
    height: 27px;
    background: var(--blue);
    color: var(--white);
    font-family: "Montserrat", sans-serif;
    font-weight: 700;
    font-size: 11px;
    text-align: center;
    line-height: 27px;
  }
</style>
</head>
<body>
  <section class="label label-500ml">
    <header class="label-head">
      <div class="brand"><span class="brand-dot"></span><span class="brand-name">vorlix</span></div>
      <h1 class="product-name">SANITARY</h1>
    </header>
    <div class="product-type">CLEANER</div>
    <div class="use-photo" role="img" aria-label="Photo of a modern bathroom with glass shower, washbasin and bathtub"></div>
    <div class="claim">CLEANS, DESCALES &amp; FRESHENS.</div>
    <div class="label-body">
      <p class="note">Ideal for quick and powerful cleaning.<br>A ready-to-use product for everyday use.</p>
      <p class="uses"><span class="alt">SANITARY,</span> BATHROOM, <span class="alt">TOILET,</span> WET AREAS</p>
    </div>
    <div class="net-weight">Net weight 500 ml</div>
  </section>

  <section class="label label-1l">
    <header class="label-head">
      <div class="brand"><span class="brand-dot"></span><span class="brand-name">vorlix</span></div>
      <h1 class="product-name">SANITARY</h1>
    </header>
    <div class="product-type">CLEANER</div>
    <div class="use-photo" role="img" aria-label="Photo of a modern bathroom with glass shower, washbasin and bathtub"></div>
    <div class="claim">CLEANS, DESCALES &amp; FRESHENS.</div>
    <div class="label-body">
      <p class="note">Ideal for quick and powerful cleaning.<br>A ready-to-use product for everyday use.</p>
      <p class="uses"><span class="alt">SANITARY,</span> BATHROOM, <span class="alt">TOILET,</span> WET AREAS</p>
    </div>
    <div class="net-weight">Net weight 1l</div>
  </section>
</body>
</html>
```